Transform Your Giving

I need a tri-fold brochure that will fit in a standard number 10 business envelope. Meadowlark and Allied Services is a charitable nonprofit. The goal of this brochure is to stimulate people into thinking about other ways to make a donation. The design should communicate the essential information on donation options, create a sense of professional integrity, be graphically sharp, easy to read and laid out in a way that doesn't make the material appear crowded.

```html
<!DOCTYPE html>
<html lang="en">
<head>
<meta charset="utf-8">
<title>Transform Your Giving – Tri-fold Brochure</title>
<link rel="stylesheet" href="https://fonts.googleapis.com/css2?family=Bebas+Neue&family=Montserrat:ital,wght@0,400;0,500;0,600;0,700;1,600;1,700&display=swap">
<style>
:root{
  --purple:#2f2a7e;
  --purple-deep:#241f66;
  --purple-light:#4a3aa0;
  --green:#4cb848;
  --green-dark:#3aa13a;
  --white:#ffffff;
  --ink:#2b2b3a;
  --page:#ebebeb;
  --body:'Montserrat',sans-serif;
  --display:'Bebas Neue',sans-serif;
}
*{box-sizing:border-box;margin:0;padding:0}
html,body{width:720px;height:1200px;overflow:hidden;background:var(--page);font-family:var(--body);color:var(--ink)}
.sheet{position:absolute;width:634px;height:490px;box-shadow:0 2px 6px rgba(0,0,0,.25);background:var(--white);overflow:hidden}
.sheet--outside{left:55px;top:70px}
.sheet--inside{left:50px;top:644px}
.panel{position:absolute;top:0;height:490px;overflow:hidden}
.panel--a{left:0;width:211px}
.panel--b{left:211px;width:212px}
.panel--c{left:423px;width:211px}
.panel--purple{background:linear-gradient(100deg,var(--purple-deep) 0%,var(--purple) 55%,var(--purple-light) 100%);color:var(--white)}
.abs{position:absolute}
.photo{position:absolute}
.body-text{font-size:6.1px;line-height:1.3}
.center{text-align:center}
.pill{position:absolute;background:var(--green);color:var(--white);font-weight:700;font-size:7.6px;letter-spacing:.2px;padding:2px 5px;border-radius:0 7px 7px 0}
.opt-head{position:absolute;color:var(--green);font-weight:700;font-size:7.6px;line-height:1.25}
.opt-head em{display:block;font-size:5.9px;font-style:italic;font-weight:700;line-height:1.3;margin-top:1px}
.checklist{list-style:none}
.checklist li{position:relative;padding-left:9px;margin-bottom:7px;font-size:6.1px;font-weight:600}
.checklist li svg{position:absolute;left:0;top:1px}
.checks li{font-weight:400;line-height:1.3;margin-bottom:8px;padding-left:13px}
.org-name{font-family:var(--body);font-weight:700;color:var(--purple);text-align:center}
</style>
</head>
<body>

<!-- OUTSIDE -->
<section class="sheet sheet--outside" aria-label="Brochure outside">

  <!-- Back flap: impact -->
  <div class="panel panel--a">
    <div class="photo" role="img" aria-label="Photo of a young man walking arm in arm with an elderly woman in a sunny park" style="left:0;top:0;width:211px;height:320px;background:linear-gradient(160deg,#a9c24a 0%,#6d8f2e 45%,#c9b08f 80%,#9c7fb8 100%)"></div>
    <svg class="abs" style="left:0;top:270px" width="211" height="90" viewBox="0 0 211 90">
      <path d="M0 50 Q90 10 165 25 Q195 32 211 55 L211 90 L0 90Z" fill="var(--green)"/>
      <path d="M0 58 Q95 22 160 38 Q190 46 211 75 L211 90 L0 90Z" fill="var(--white)"/>
    </svg>
    <div class="abs" style="left:0;top:325px;width:146px;height:21px;background:var(--purple);border-radius:0 11px 11px 0;color:var(--white);font-family:var(--display);font-size:17px;line-height:21px;padding-left:15px">THE IMPACT OF YOUR GIFT</div>
    <p class="abs body-text" style="left:15px;top:360px;width:183px">Your generosity drives our mission. With every Smart gift you're supporting Meadowlark and Allied Services. Join our community of Smart Givers today and make an enduring impact. With Smart Giving your generosity reaches further. Begin your Smart Giving journey with us today.</p>
    <ul class="abs checklist" style="left:15px;top:415px">
      <li><svg width="6" height="6" viewBox="0 0 6 6"><rect x=".4" y=".4" width="5.2" height="5.2" fill="none" stroke="var(--purple)" stroke-width=".6"/><path d="M1.2 3l1.2 1.2L5 1.4" fill="none" stroke="var(--purple)" stroke-width=".7"/></svg>Stocks and Securities</li>
      <li><svg width="6" height="6" viewBox="0 0 6 6"><rect x=".4" y=".4" width="5.2" height="5.2" fill="none" stroke="var(--purple)" stroke-width=".6"/><path d="M1.2 3l1.2 1.2L5 1.4" fill="none" stroke="var(--purple)" stroke-width=".7"/></svg>DAFs</li>
      <li><svg width="6" height="6" viewBox="0 0 6 6"><rect x=".4" y=".4" width="5.2" height="5.2" fill="none" stroke="var(--purple)" stroke-width=".6"/><path d="M1.2 3l1.2 1.2L5 1.4" fill="none" stroke="var(--purple)" stroke-width=".7"/></svg>QCDs</li>
      <li><svg width="6" height="6" viewBox="0 0 6 6"><rect x=".4" y=".4" width="5.2" height="5.2" fill="none" stroke="var(--purple)" stroke-width=".6"/><path d="M1.2 3l1.2 1.2L5 1.4" fill="none" stroke="var(--purple)" stroke-width=".7"/></svg>Crypto</li>
      <li><svg width="6" height="6" viewBox="0 0 6 6"><rect x=".4" y=".4" width="5.2" height="5.2" fill="none" stroke="var(--purple)" stroke-width=".6"/><path d="M1.2 3l1.2 1.2L5 1.4" fill="none" stroke="var(--purple)" stroke-width=".7"/></svg>Charitable Annuity</li>
    </ul>
  </div>

  <!-- Back panel: contact -->
  <div class="panel panel--b panel--purple">
    <p class="abs body-text center" style="left:16px;top:16px;width:180px">To learn more about Smart Giving Options and how they can benefit you and Meadowlark and Allied Services, please reach out to our team. We're here to help you navigate these giving methods and answer any question you may have.</p>
    <svg class="abs" style="left:20px;top:66px" width="180" height="60" viewBox="0 0 180 60">
      <text x="0" y="22" fill="var(--green)" font-family="Montserrat,sans-serif" font-weight="700" font-size="30">“</text>
      <path d="M32 14 H170 Q177 14 177 21 V43 Q177 50 170 50 H110" fill="none" stroke="var(--green)" stroke-width=".8"/>
      <text x="78" y="58" fill="var(--green)" font-family="Montserrat,sans-serif" font-weight="700" font-size="30">”</text>
    </svg>
    <p class="abs" style="left:21px;top:92px;width:170px;font-size:7.6px;font-style:italic;line-height:1.3">Being kind to others is a way of being good to yourself.<br><b>- Miriam Ashdale</b></p>
    <p class="abs org-name" style="left:20px;top:152px;width:172px;color:var(--white);font-size:9px;line-height:1.25">Meadowlark and Allied Services</p>
    <div class="abs center" style="left:28px;top:204px;width:158px;height:30px;background:var(--green);border-radius:6px;font-size:5.9px;line-height:1.35;padding-top:3px">If you do not have a will, go to<br><b>www.SimpleWillNow.org</b><br>In 20 minutes you can have a legal will for free.</div>
    <p class="abs center" style="left:0;top:264px;width:212px;font-size:7.4px;font-weight:700;text-decoration:underline">CONTACT US</p>
    <p class="abs body-text center" style="left:0;top:280px;width:212px">Have more question?<br>Please contact us at Meadowlark &amp; Allied Services</p>
    <svg class="abs" style="left:101px;top:297px" width="10" height="10" viewBox="0 0 10 10"><circle cx="5" cy="5" r="5" fill="var(--green)"/><path d="M5 2.2a1.8 1.8 0 0 1 1.8 1.8C6.8 5.3 5 7.6 5 7.6S3.2 5.3 3.2 4A1.8 1.8 0 0 1 5 2.2z" fill="var(--white)"/></svg>
    <p class="abs body-text center" style="left:0;top:310px;width:212px">1420 Prairie View Rd.<br>Suite 2, Fargo, ND&nbsp; 58102</p>
    <svg class="abs" style="left:101px;top:327px" width="10" height="10" viewBox="0 0 10 10"><circle cx="5" cy="5" r="5" fill="var(--green)"/><path d="M3.3 2.5l1 1-.5.7a4 4 0 0 0 2 2l.7-.5 1 1-.6.8C5 7.3 2.7 5 2.5 3.1z" fill="var(--white)"/></svg>
    <p class="abs body-text center" style="left:0;top:340px;width:212px">555-014-2200 (ext. 100)</p>
    <svg class="abs" style="left:101px;top:351px" width="10" height="10" viewBox="0 0 10 10"><circle cx="5" cy="5" r="5" fill="var(--green)"/><rect x="2.7" y="3.3" width="4.6" height="3.4" fill="var(--white)"/><path d="M2.7 3.3L5 5.2l2.3-1.9" fill="none" stroke="var(--green)" stroke-width=".5"/></svg>
    <p class="abs body-text center" style="left:0;top:363px;width:212px">dmarlow@meadowlarkallied.org</p>
    <svg class="abs" style="left:101px;top:375px" width="10" height="10" viewBox="0 0 10 10"><circle cx="5" cy="5" r="5" fill="var(--green)"/><circle cx="5" cy="5" r="2.6" fill="none" stroke="var(--white)" stroke-width=".6"/><path d="M2.4 5h5.2M5 2.4v5.2" stroke="var(--white)" stroke-width=".5"/></svg>
    <p class="abs body-text center" style="left:0;top:387px;width:212px">www.meadowlarkallied.org</p>
    <p class="abs center" style="left:0;top:414px;width:212px;font-size:7.4px;font-weight:700;text-decoration:underline">Follow us:</p>
    <svg class="abs" style="left:76px;top:427px" width="60" height="12" viewBox="0 0 60 12">
      <path d="M11 6H25M35 6H49" stroke="var(--green)" stroke-width=".7"/>
      <circle cx="6" cy="6" r="5" fill="var(--green)"/><circle cx="30" cy="6" r="5" fill="var(--green)"/><circle cx="54" cy="6" r="5" fill="var(--green)"/>
    </svg>
    <p class="abs center" style="left:16px;top:457px;width:180px;font-size:3.9px;line-height:1.3">This material has been prepared for informational purposes only and is not intended to provide tax, accounting, or legal advice. Meadowlark and Allied Services is not a professional fiduciary organization. Please consult with your tax advisor or financial professional before making a decision about Smart Giving.</p>
  </div>

  <!-- Cover -->
  <div class="panel panel--c">
    <h1 class="abs center" style="left:0;top:12px;width:211px;font-family:var(--display);font-weight:400;font-size:25px;line-height:1;color:var(--green)">TRANSFORM YOUR GIVING</h1>
    <div class="abs center" style="left:22px;top:37px;width:168px;height:15px;background:var(--purple);border-radius:8px;color:var(--white);font-weight:700;font-size:10.6px;line-height:15px;letter-spacing:.3px">BE STRATEGIC, BE SMART</div>
    <p class="abs center" style="left:0;top:57px;width:211px;font-size:8.4px;line-height:1.25">Discover the impact of Smart Giving with Meadowlark and Allied Services</p>
    <div class="photo" role="img" aria-label="Photo of a smiling young woman with curly hair resting her chin on her hands" style="left:0;top:85px;width:211px;height:340px;background:linear-gradient(120deg,#d9d4d6 0%,#b79a88 40%,#7a4f3c 65%,#cfc8ca 100%)"></div>
    <svg class="abs" style="left:0;top:80px" width="211" height="50" viewBox="0 0 211 50">
      <path d="M0 0H211V14Q150 42 90 36Q40 30 0 8Z" fill="var(--white)"/>
      <path d="M18 12Q80 42 150 34Q185 30 211 14V22Q180 40 140 42Q70 44 18 12Z" fill="var(--green)"/>
    </svg>
    <!-- option bubbles -->
    <svg class="abs" style="left:0;top:110px" width="211" height="320" viewBox="0 0 211 320">
      <g fill="rgba(255,255,255,.72)" stroke="rgba(255,255,255,.9)" stroke-width=".6">
        <circle cx="40" cy="20" r="26"/><circle cx="171" cy="68" r="26"/>
        <circle cx="40" cy="148" r="26"/><circle cx="171" cy="185" r="26"/>
        <circle cx="40" cy="255" r="26"/>
      </g>
      <g fill="none" stroke="var(--purple)" stroke-width="1.3">
        <circle cx="33" cy="8" r="5"/><circle cx="47" cy="8" r="5"/><circle cx="40" cy="18" r="5"/>
        <circle cx="167" cy="58" r="6"/><circle cx="176" cy="67" r="6"/>
      </g>
      <g fill="var(--purple)">
        <rect x="30" y="133" width="2.5" height="12"/><rect x="35" y="138" width="2.5" height="7"/><rect x="40" y="135" width="2.5" height="10"/><rect x="45" y="131" width="2.5" height="14"/><rect x="28" y="145" width="23" height="1.5"/>
        <rect x="161" y="175" width="20" height="5"/><rect x="163" y="180" width="16" height="11"/>
        <ellipse cx="40" cy="251" rx="7" ry="2"/><ellipse cx="40" cy="246" rx="7" ry="2"/><ellipse cx="40" cy="241" rx="7" ry="2"/><circle cx="47" cy="233" r="4"/>
      </g>
      <g fill="var(--purple)" font-family="Montserrat,sans-serif" font-size="6.3" font-weight="500" text-anchor="middle">
        <text x="40" y="32">Crypto</text><text x="171" y="80">DAF's</text>
        <text x="40" y="160">Stocks &amp;</text><text x="40" y="167">Securities</text>
        <text x="171" y="196">QCDs</text>
        <text x="40" y="262">Charitable</text><text x="40" y="269">Annuity</text>
      </g>
    </svg>
    <svg class="abs" style="left:0;top:400px" width="211" height="90" viewBox="0 0 211 90">
      <path d="M0 40Q90 -5 170 8Q195 12 211 22V90H0Z" fill="var(--purple)"/>
      <path d="M0 52Q90 8 170 18Q195 22 211 30V90H0Z" fill="var(--white)"/>
    </svg>
    <p class="abs org-name" style="left:10px;top:448px;width:191px;font-size:10px;line-height:1.25">Meadowlark and Allied Services</p>
  </div>
</section>

<!-- INSIDE -->
<section class="sheet sheet--inside" aria-label="Brochure inside">

  <div class="panel panel--a panel--purple">
    <p class="abs body-text" style="left:15px;top:16px;width:182px">We would like to introduce you to five Strategic and Smart ways to give that could potentially be more beneficial to you compared to traditional cash donations. We encourage you to keep this information as a guide for your future contributions.</p>
    <svg class="abs" style="left:15px;top:66px" width="38" height="32" viewBox="0 0 38 32"><g fill="var(--green)"><rect x="2" y="14" width="3.5" height="14"/><rect x="9" y="18" width="3.5" height="10"/><rect x="16" y="12" width="3.5" height="16"/><rect x="23" y="16" width="3.5" height="12"/><rect x="30" y="10" width="3.5" height="18"/><rect x="0" y="28" width="36" height="2"/><rect x="0" y="4" width="2" height="26"/></g><path d="M4 10l7 3 6-7 7 5 9-8" fill="none" stroke="var(--green)" stroke-width="1.4"/></svg>
    <h2 class="opt-head" style="left:59px;top:63px;width:140px">Gifts of Stocks or Appreciated Assets Strategic &amp; Smart<em>Consider your long-term publicly traded stock as a way to give to your favorite charity.</em></h2>
    <p class="abs body-text" style="left:15px;top:114px;width:186px">You can make a significantly bigger impact when you donate long-term appreciated securities, including stock, mutual funds, and bonds, directly to your favorite charity.</p>
    <div class="pill" style="left:14px;top:145px">HOW DOES IT WORK?</div>
    <p class="abs body-text" style="left:14px;top:169px;width:186px">When you donate stock to a charity, you will generally take a tax deduction for the full market value. Because you are donating stock, your contribution and tax deduction may be significantly higher than contributing the after-tax proceeds. The same benefits apply when you donate mutual funds or bonds.</p>
    <svg class="abs" style="left:15px;top:240px" width="38" height="38" viewBox="0 0 38 38"><g fill="none" stroke="var(--green)" stroke-width="1.3"><circle cx="13" cy="14" r="9"/><circle cx="13" cy="14" r="4"/><circle cx="25" cy="25" r="9"/><circle cx="25" cy="25" r="4"/></g></svg>
    <h2 class="opt-head" style="left:59px;top:238px;width:140px">Donor-Advised Fund (DAF) Strategic &amp; Smart<em>Consider a DAF – a simple, flexible, and tax-advantageous way to give to your favorite charities.</em></h2>
    <p class="abs body-text" style="left:15px;top:289px;width:186px">A Donor-Advised Fund (DAF), is like a charitable investment account for the sole purpose of supporting your favorite charities.</p>
    <div class="pill" style="left:14px;top:321px">HOW DOES IT WORK?</div>
    <p class="abs body-text" style="left:14px;top:345px;width:186px">You establish a DAF and contribute cash, stocks, or non-publicly traded assets, cryptocurrency, and private company stock to be eligible for an immediate tax deduction. Those funds are contributed for tax-free growth. You can recommend grants be made from your DAF to any IRS qualified public charity.</p>
    <div class="photo" role="img" aria-label="Photo of an elderly woman and a younger woman embracing, cheek to cheek" style="left:0;top:410px;width:211px;height:80px;background:linear-gradient(100deg,#6b5a52 0%,#c9b6aa 50%,#efe7e2 100%)"></div>
    <svg class="abs" style="left:0;top:400px" width="211" height="90" viewBox="0 0 211 90">
      <path d="M0 0H211V90Q190 30 120 18Q60 8 0 20Z" fill="var(--purple)"/>
      <path d="M0 20Q60 8 120 18Q190 30 211 90H205Q185 38 120 26Q60 16 0 28Z" fill="var(--green)"/>
    </svg>
  </div>

  <div class="panel panel--b">
    <div class="photo" role="img" aria-label="Photo of an elderly woman and a young man sharing a snack at a small table" style="left:0;top:0;width:212px;height:255px;background:linear-gradient(180deg,#dcd6d2 0%,#c4b8ae 55%,#eae6e3 85%,#ffffff 100%)"></div>
    <svg class="abs" style="left:12px;top:270px" width="32" height="40" viewBox="0 0 32 40"><g fill="var(--green)"><rect x="1" y="12" width="30" height="8"/><rect x="3" y="21" width="26" height="18"/></g><rect x="14.5" y="12" width="3" height="27" fill="var(--white)"/><path d="M16 12C10 2 4 4 7 9ZM16 12C22 2 28 4 25 9Z" fill="none" stroke="var(--green)" stroke-width="2.4"/></svg>
    <h2 class="opt-head" style="left:51px;top:269px;width:155px">Qualified Charitable Distributions (QCDs) Strategic &amp; Smart<em>Consider a QCD – when planning your IRA withdrawal strategy…and donate to your favorite charity.</em></h2>
    <p class="abs body-text" style="left:12px;top:326px;width:190px">IRA owners at age 70 or over can transfer dollars from their IRA to charity tax-free each year. These transfers known as Qualified Charitable Distributions (QCDs) offer eligible older Americans a great way to easily give to charity.</p>
    <div class="pill" style="left:11px;top:373px">HOW DOES IT WORK?</div>
    <p class="abs body-text" style="left:12px;top:398px;width:192px">Are you 72 and required to take a minimum distribution (RMD) from your IRA but do not need the funds? Consider a Qualified Charitable Distribution. Normally, distributions from a traditional IRA are taxable when received. With a QCD, these distributions become tax-free when paid directly from the IRA to your favorite eligible charity. An IRA owner wishing to make a QCD should contact their IRA trustee, allowing time to complete the transaction before the end of the year to receive the tax benefit.</p>
  </div>

  <div class="panel panel--c panel--purple">
    <svg class="abs" style="left:16px;top:14px" width="34" height="30" viewBox="0 0 34 30"><g fill="none" stroke="var(--green)" stroke-width="1.5"><circle cx="9" cy="9" r="7"/><circle cx="25" cy="9" r="7"/><circle cx="17" cy="21" r="7"/></g></svg>
    <h2 class="opt-head" style="left:54px;top:14px;width:152px">Cryptocurrency Strategic &amp; Smart<em>Consider donating Bitcoin and other cryptocurrencies to your favorite charity.</em></h2>
    <p class="abs body-text" style="left:15px;top:54px;width:186px">Bitcoin and other cryptocurrencies can be donated to charity just like other appreciated assets such as stocks and other business interests. Before you sell bitcoin and donate the after-tax proceeds, consider donating your bitcoin directly to a favorite charity.</p>
    <div class="pill" style="left:14px;top:103px">HOW DOES IT WORK?</div>
    <p class="abs body-text" style="left:15px;top:125px;width:186px">Many donors find it useful to open a Donor-Advised Fund (DAF). This strategy includes two significant benefits, both for you and your favorite charity.</p>
    <ul class="abs checklist checks" style="left:15px;top:159px;width:186px">
      <li><svg width="7" height="7" viewBox="0 0 6 6"><rect x=".4" y=".4" width="5.2" height="5.2" fill="none" stroke="var(--white)" stroke-width=".6"/><path d="M1.2 3l1.2 1.2L5 1.4" fill="none" stroke="var(--white)" stroke-width=".7"/></svg>Your tax deduction will be equal to the fair market value of the donated bitcoin (as determined by a qualified appraisal).</li>
      <li><svg width="7" height="7" viewBox="0 0 6 6"><rect x=".4" y=".4" width="5.2" height="5.2" fill="none" stroke="var(--white)" stroke-width=".6"/><path d="M1.2 3l1.2 1.2L5 1.4" fill="none" stroke="var(--white)" stroke-width=".7"/></svg>Your cryptocurrency donation is tax-smart because it may eliminate capital gains taxes on the value /appreciation AND your favorite charity will receive 100% of the value of the contribution.</li>
    </ul>
    <p class="abs body-text" style="left:15px;top:230px;width:188px">Often charities are not able to accept direct donations of bitcoin/crypto so using a DAF is a great way to donate these assets.</p>
    <svg class="abs" style="left:14px;top:268px" width="36" height="34" viewBox="0 0 36 34"><g fill="var(--green)"><ellipse cx="10" cy="30" rx="8" ry="2.3"/><ellipse cx="10" cy="25" rx="8" ry="2.3"/><ellipse cx="24" cy="30" rx="8" ry="2.3"/><ellipse cx="24" cy="25" rx="8" ry="2.3"/><ellipse cx="24" cy="20" rx="8" ry="2.3"/><circle cx="28" cy="6" r="5"/><rect x="1" y="6" width="10" height="1.5"/><rect x="3" y="10" width="8" height="1.5"/></g></svg>
    <h2 class="opt-head" style="left:54px;top:269px;width:150px">Charitable Gift Annuity Strategic &amp; Smart<em>Consider establishing a Charitable Gift Annuity</em></h2>
    <p class="abs body-text" style="left:15px;top:312px;width:186px">You make a donation to a single charity. The gift is set aside in a reserve account and invested.</p>
    <div class="pill" style="left:14px;top:334px">HOW DOES IT WORK?</div>
    <p class="abs body-text" style="left:15px;top:357px;width:188px">A charitable gift annuity is a contract between a donor and a charity. As a donor, you make a sizable gift to charity using cash, securities, or possibly other assets. This money is then invested. In return, you become eligible to take a partial tax deduction for your donation, plus you receive a fixed stream of income from the charity for the rest of your life. At the end of your life (as well as your spouse's, if you're giving as a couple), the charity receives the remainder of the gift.</p>
    <svg class="abs" style="left:0;top:430px" width="211" height="60" viewBox="0 0 211 60">
      <path d="M0 60Q60 12 211 6V60Z" fill="var(--white)"/>
      <path d="M0 60Q60 12 211 6V0Q60 4 0 58Z" fill="var(--green)"/>
    </svg>
    <div class="abs center" style="left:112px;top:462px;width:99px;height:13px;background:var(--purple-deep);border-radius:7px 0 0 7px;font-size:7px;line-height:13px;color:var(--white)">www.meadowlarkallied.org</div>
  </div>
</section>

</body>
</html>
```